AGP letterhead

We need a letterhead design for our new company based in Los Angeles called "Amber Gate Pictures". We develop film and television projects. We work with investors, financiers, film production companies, film distribution and sales companies as well as studios. We would like to incorporate our logo (see attached) but make the letterhead simple and elegant. We need to include: logo, company address, phone number and company website.
Updates

Hello designers, Thanks for your submissions. For our letterhead, we are looking for something more simple and elegant. No heavy bars or lines. Make it feel light and clean. Not a lot of ink on the page. Use the logo and contact info but think "clean", "streamlined" and mostly white paper. Looking forward to seeing more... thanks! Amber Gate Pictures team

Target Market(s)

Studio executives, talent agents and agencies, financiers, investors.

Industry/Entity Type

It Company

Requirements
Must have
• Amber Gate Pictures logo (see attached). Logo may be cropped and altered appropriately for elegant letterhead design.
• Please include:
• COMPANY ADDRESS:
• Tolvane Arts Park
• 2850 Delmore Street
• Crest Hall, 2nd Floor
• Manhattan Beach, CA 90266
• COMPANY WEBSITE:
• www.ambergatepicturesco.example
• COMPANY PHONE NUMBER:
• 555-604-2187

```html
<!DOCTYPE html>
<html lang="en">
<head>
<meta charset="utf-8">
<title>Amber Gate Pictures — Letterhead</title>
<link rel="stylesheet" href="https://fonts.googleapis.com/css2?family=Josefin+Sans:wght@300;400;600&display=swap">
<style>
  :root {
    --backdrop: #e4e4e4;
    --paper: #ffffff;
    --ink: #2b3a40;
    --ink-soft: #55636a;
    --accent: #1f9ad6;
    --accent-deep: #0d4f7a;
  }
  * { margin: 0; padding: 0; box-sizing: border-box; }
  html, body {
    width: 1200px; height: 936px; overflow: hidden;
    background: var(--backdrop);
    font-family: "Josefin Sans", "Helvetica Neue", sans-serif;
  }
  .letterhead {
    position: absolute; left: 260px; top: 28px;
    width: 680px; height: 880px;
    background: var(--paper);
    box-shadow: 0 2px 10px rgba(0,0,0,0.12);
  }
  .brand {
    position: absolute; left: 44px; top: 46px;
    display: flex; flex-direction: column; align-items: flex-start; gap: 8px;
  }
  .brand-dot {
    width: 40px; height: 40px; border-radius: 50%;
    background: var(--accent);
  }
  .brand-name {
    font-weight: 600; font-size: 11px; letter-spacing: 1.6px;
    text-transform: uppercase; color: var(--accent-deep);
  }
  .contact {
    position: absolute; left: 452px; top: 40px;
    list-style: none; font-weight: 300; font-size: 9.5px;
    line-height: 14px; color: var(--ink);
  }
  .contact li { display: flex; gap: 6px; align-items: flex-start; }
  .contact svg { width: 8px; height: 8px; margin-top: 2px; flex: none; fill: var(--ink); }
  .footer-rule {
    position: absolute; left: 108px; right: 22px; bottom: 60px;
    height: 9px; background: var(--ink);
  }
  .footer-web {
    position: absolute; right: 22px; bottom: 76px;
    font-weight: 300; font-size: 13px; color: var(--ink);
  }
  .corner-mark {
    position: absolute; left: 40px; bottom: 34px;
    width: 70px; height: 70px; border-radius: 50%;
    border: 2px solid var(--ink);
  }
</style>
</head>
<body>
  <main class="letterhead">
    <div class="brand">
      <span class="brand-dot"></span>
      <span class="brand-name">Amber Gate Pictures</span>
    </div>

    <ul class="contact">
      <li>
        <svg viewBox="0 0 8 8" aria-hidden="true"><path d="M4 0a3 3 0 0 0-3 3c0 2.2 3 5 3 5s3-2.8 3-5a3 3 0 0 0-3-3zm0 4.2a1.2 1.2 0 1 1 0-2.4 1.2 1.2 0 0 1 0 2.4z"/></svg>
        <span>2850 Delmore Street, Crest Hall<br>Manhattan Beach, CA 90266</span>
      </li>
      <li>
        <svg viewBox="0 0 8 8" aria-hidden="true"><path d="M1.6 0.4l1.2 1.6-0.8 1a5 5 0 0 0 3 3l1-0.8 1.6 1.2-0.8 1.2C3.6 7.6 0.4 4.4 0.4 1.2z"/></svg>
        <span>555-604-2187</span>
      </li>
      <li>
        <svg viewBox="0 0 8 8" aria-hidden="true"><path d="M0 1.5h8v5H0zM0.6 2l3.4 2.4L7.4 2"/></svg>
        <span>office@ambergatepicturesco.example</span>
      </li>
    </ul>

    <span class="footer-web">ambergatepicturesco.example</span>
    <div class="footer-rule"></div>
    <div class="corner-mark" role="img" aria-label="Decorative corner emblem"></div>
  </main>
</body>
</html>
```